Business Card Design Project

I require a business card with the following information on them for various different people;
name
m:
f:
e:
I have a logo already and will attached that. We are in the construction industry. I require something clean and simple but eye catching at the same time. You can use another colour with our logo if you like and you can style the logo as well if you wish. I am open.
Also it needs to be front and back design.
Industry/Entity Type
Construction
Requirements
Must have
- Logo, name, mobile, fax and email address.
Front and back design

```html
<!DOCTYPE html>
<html lang="en">
<head>
<meta charset="utf-8">
<title>Stonefield Developments – Business Cards</title>
<link href="https://fonts.googleapis.com/css2?family=Open+Sans:wght@400;600&display=swap" rel="stylesheet">
<style>
  :root {
    --backdrop: #d7d8d9;
    --card: #ffffff;
    --card-edge: #f1f1f1;
    --brand-green: #4cae2f;
    --brand-green-light: #8fd36a;
    --ink: #2b2b2b;
    --ink-soft: #4a4a4a;
    --stripe: #1d1d1d;
  }
  * { box-sizing: border-box; margin: 0; padding: 0; }
  html, body { width: 1200px; height: 944px; overflow: hidden; }
  body {
    background: var(--backdrop);
    font-family: "Open Sans", Arial, sans-serif;
    color: var(--ink);
    position: relative;
  }
  .card {
    position: absolute;
    width: 620px;
    height: 354px;
    border-radius: 24px;
    background: linear-gradient(160deg, var(--card) 55%, var(--card-edge));
    box-shadow: 0 14px 28px rgba(0,0,0,0.22);
    overflow: hidden;
  }
  .card--front { left: 90px; top: 100px; }
  .card--back { left: 490px; top: 480px; }

  .brand {
    display: flex;
    align-items: center;
    gap: 14px;
    color: var(--brand-green);
    font-weight: 400;
    white-space: nowrap;
  }
  .brand__mark {
    background: var(--brand-green);
    flex: none;
  }
  .card--front .brand {
    position: absolute;
    left: 0; right: 0; top: 112px;
    justify-content: center;
    font-size: 40px;
  }
  .card--front .brand__mark { width: 38px; height: 38px; }
  .card--front .website {
    position: absolute;
    left: 0; right: 0; top: 214px;
    text-align: center;
    font-size: 17px;
    letter-spacing: 1px;
    color: var(--ink);
  }

  .card--back .brand {
    position: absolute;
    left: 38px; top: 50px;
    font-size: 25px;
    gap: 10px;
  }
  .card--back .brand__mark { width: 22px; height: 22px; }
  .person { position: absolute; left: 400px; top: 104px; }
  .person__name { font-size: 22px; font-weight: 600; letter-spacing: 0.5px; }
  .person__role { font-size: 14px; color: var(--brand-green); margin-top: 2px; }

  .contact-list {
    position: absolute;
    list-style: none;
    font-size: 17px;
    line-height: 23px;
    color: var(--ink-soft);
  }
  .contact-list--phones { left: 48px; top: 194px; }
  .contact-list--online { left: 380px; top: 202px; }
  .contact-list li { display: flex; align-items: center; gap: 8px; }
  .contact-list svg { width: 14px; height: 14px; flex: none; }

  .wave { position: absolute; left: 0; bottom: 0; width: 620px; height: 354px; }
</style>
</head>
<body>
  <section class="card card--front" aria-label="Card front">
    <div class="brand"><span class="brand__mark"></span>Stonefield Developments</div>
    <p class="website">www.stonefieldbuild.com</p>
  </section>

  <section class="card card--back" aria-label="Card back">
    <svg class="wave" viewBox="0 0 620 354" aria-hidden="true">
      <defs>
        <linearGradient id="band-green" x1="0" y1="0" x2="0" y2="1">
          <stop offset="0" stop-color="var(--brand-green-light)"/>
          <stop offset="1" stop-color="var(--brand-green)"/>
        </linearGradient>
      </defs>
      <path d="M0 262 C180 238 360 316 620 286 L620 300 C360 330 180 256 0 276 Z" fill="var(--stripe)"/>
      <path d="M0 286 C190 268 370 340 620 308 L620 354 L0 354 Z" fill="url(#band-green)"/>
    </svg>

    <div class="brand"><span class="brand__mark"></span>Stonefield Developments</div>

    <div class="person">
      <p class="person__name">Mark Ellison</p>
      <p class="person__role">director</p>
    </div>

    <ul class="contact-list contact-list--phones">
      <li>
        <svg viewBox="0 0 14 14" aria-hidden="true"><path d="M3 1 L5.5 1 L6.5 4 L5 5.2 C5.8 7 7 8.2 8.8 9 L10 7.5 L13 8.5 L13 11 C13 12.2 12 13 10.8 12.9 C5.5 12.4 1.6 8.5 1.1 3.2 C1 2 1.8 1 3 1 Z" fill="var(--brand-green)"/></svg>
        512-555-0140
      </li>
      <li>
        <svg viewBox="0 0 14 14" aria-hidden="true"><rect x="3" y="1" width="8" height="4" fill="var(--brand-green)"/><rect x="1" y="5" width="12" height="6" rx="1" fill="var(--brand-green)"/><rect x="3.5" y="9" width="7" height="4" fill="#fff" stroke="var(--brand-green)"/></svg>
        512-555-0141
      </li>
    </ul>

    <ul class="contact-list contact-list--online">
      <li>
        <svg viewBox="0 0 14 14" aria-hidden="true"><rect x="1" y="3" width="12" height="8" rx="1" fill="var(--brand-green)"/><path d="M1.5 3.5 L7 8 L12.5 3.5" fill="none" stroke="#fff" stroke-width="1.2"/></svg>
        info@stonefieldbuild.com
      </li>
      <li>
        <svg viewBox="0 0 14 14" aria-hidden="true"><circle cx="7" cy="7" r="6" fill="var(--brand-green)"/></svg>
        www.stonefieldbuild.com
      </li>
    </ul>
  </section>
</body>
</html>
```